Tech business card design

We need an amazing business card design for our new business 'Pexla' a marketing tech startup based in Sydney, Australia. We provide an online marketplace for businesses to search and buy advertising media, connect with service providers and learn more about marketing. We wish to communicate 'cool tech', reliability and professionalism and design based around our logo.

Target Market(s)

Business Owners

Contact Information for Business Card

Name
Position
Email Address
Website
Phone Number

Font styles to use
Other font styles liked:
• Avenir & Avenir Next

Colors

Designer to choose colors to be used in the design.

```html
<!DOCTYPE html>
<html lang="en">
<head>
<meta charset="utf-8">
<title>Pexla Business Card</title>
<link href="https://fonts.googleapis.com/css2?family=Nunito+Sans:wght@300;400;700;800&display=swap" rel="stylesheet">
<style>
  :root {
    --navy: #1b1e4b;
    --grey: #7a7a80;
    --rule: #6d6d72;
    --card: #ffffff;
    --backdrop: #2b2b2e;
  }
  * { margin: 0; padding: 0; box-sizing: border-box; }
  html, body { width: 1200px; height: 892px; overflow: hidden; }
  body {
    background: var(--backdrop);
    font-family: "Nunito Sans", sans-serif;
    position: relative;
  }
  .card {
    position: absolute;
    width: 540px;
    height: 309px;
    background: var(--card);
    box-shadow: 0 10px 30px rgba(0,0,0,0.45);
    overflow: hidden;
  }
  .card-back { left: 60px; top: 110px; }
  .card-front { left: 600px; top: 470px; }

  .wordmark {
    font-family: "Nunito Sans", sans-serif;
    font-weight: 800;
    color: var(--navy);
    letter-spacing: -1px;
    line-height: 1;
  }
  .card-back .brand {
    position: absolute;
    right: 62px;
    top: 150px;
    text-align: right;
  }
  .card-back .wordmark { font-size: 52px; }
  .card-back .domain {
    font-size: 12.5px;
    font-weight: 400;
    color: var(--grey);
    margin-top: 4px;
    letter-spacing: 0.3px;
  }

  .card-front .wordmark {
    position: absolute;
    right: 60px;
    top: 28px;
    font-size: 88px;
  }
  .card-front .top-rule {
    position: absolute;
    left: 215px;
    right: 28px;
    top: 160px;
    height: 1px;
    background: var(--rule);
  }
  .card-front .base-band {
    position: absolute;
    left: 0; right: 0; bottom: 0;
    height: 14px;
    background: var(--navy);
  }
  .card-front .name-marker {
    position: absolute;
    left: 0;
    top: 196px;
    width: 12px;
    height: 30px;
    background: var(--navy);
  }
  .identity {
    position: absolute;
    left: 62px;
    top: 192px;
  }
  .person-name {
    font-size: 18px;
    font-weight: 700;
    color: var(--navy);
    letter-spacing: 0.5px;
    line-height: 1.1;
  }
  .person-role {
    font-size: 14px;
    font-weight: 300;
    color: var(--grey);
    letter-spacing: 0.5px;
    line-height: 1.2;
  }
  .identity-rule {
    width: 200px;
    height: 1px;
    background: var(--rule);
    margin: 8px 0 7px;
  }
  .contact-list { list-style: none; }
  .contact-list li {
    display: flex;
    align-items: center;
    gap: 9px;
    font-size: 12.5px;
    color: var(--grey);
    line-height: 17px;
  }
  .contact-list svg { width: 12px; height: 12px; flex: none; }
</style>
</head>
<body>
  <section class="card card-back">
    <div class="brand">
      <div class="wordmark">pexla</div>
      <div class="domain">pexlamedia.com.au</div>
    </div>
  </section>

  <section class="card card-front">
    <div class="wordmark">pexla</div>
    <div class="top-rule"></div>
    <div class="name-marker"></div>
    <div class="identity">
      <div class="person-name">MARCUS REED</div>
      <div class="person-role">FOUNDER, DIRECTOR</div>
      <div class="identity-rule"></div>
      <ul class="contact-list">
        <li>
          <svg viewBox="0 0 12 12" aria-hidden="true"><rect x="3" y="0.8" width="6" height="10.4" rx="1" fill="none" stroke="#1b1e4b" stroke-width="1.3"/><circle cx="6" cy="9.3" r="0.7" fill="#1b1e4b"/></svg>
          +61 (0)400 555 019
        </li>
        <li>
          <svg viewBox="0 0 12 12" aria-hidden="true"><rect x="0.5" y="2.5" width="11" height="7.5" fill="#1b1e4b"/><path d="M0.8 2.8 L6 7 L11.2 2.8" fill="none" stroke="#fff" stroke-width="1"/></svg>
          marcus@pexlamedia.com.au
        </li>
        <li>
          <svg viewBox="0 0 12 12" aria-hidden="true"><circle cx="6" cy="6" r="5.5" fill="#1b1e4b"/><path d="M3.5 4.5 Q5 3.5 6 5 T8.5 7" fill="none" stroke="#fff" stroke-width="1"/></svg>
          www.pexlamedia.com.au
        </li>
      </ul>
    </div>
    <div class="base-band"></div>
  </section>
</body>
</html>
```